"Thornbury Accupuncture" needs a Promotional Card - A6 size

Requirements
Must have
• Bright colours, pictures of happy people, acupuncture-related pictures.

```html
<!DOCTYPE html>
<html lang="en">
<head>
<meta charset="utf-8">
<title>Thornbury Acupuncture – A6 Promotional Card</title>
<link href="https://fonts.googleapis.com/css2?family=Source+Sans+3:ital,wght@0,300;0,400;0,600;0,700;0,900;1,300;1,400&display=swap" rel="stylesheet">
<style>
:root{
  --red:#e23d28;
  --red-deep:#c9301f;
  --ink:#1c1c1c;
  --grey:#6e6e6e;
  --rule:#9a9a9a;
  --paper:#ffffff;
  --backdrop:#8d8d8d;
}
*{box-sizing:border-box;margin:0;padding:0}
html,body{width:1200px;height:1200px;overflow:hidden}
body{background:var(--backdrop);font-family:"Source Sans 3",sans-serif;color:var(--ink);position:relative}
.page{position:absolute;top:198px;width:570px;height:803px;background:var(--paper);overflow:hidden;box-shadow:0 6px 14px rgba(0,0,0,.35)}
.page--front{left:22px}
.page--back{left:609px}
.abs{position:absolute}
.bottom-bar{position:absolute;left:0;bottom:0;width:100%;height:15px;background:var(--red)}

/* front */
.brand{left:38px;top:48px;display:flex;align-items:center;gap:8px}
.brand__dot{width:22px;height:22px;border-radius:50%;background:var(--red)}
.brand__name{font-weight:700;font-size:19px;line-height:19px;color:var(--red)}
.tagline{right:44px;top:52px;text-align:right;font-style:italic;font-weight:400;font-size:18px;line-height:23px;letter-spacing:-.2px}
.tagline em{color:var(--red)}
.hero{left:0;top:146px;width:570px;height:270px}
.offer{left:377px;top:397px;width:220px;height:220px;border-radius:50%;background:var(--red);color:#fff;text-align:center}
.offer__lead{position:absolute;top:33px;width:100%;font-size:16.5px;line-height:21px;font-weight:400}
.offer__value{position:absolute;top:74px;width:100%;font-size:57px;line-height:57px;font-weight:700}
.offer__off{position:absolute;top:133px;width:100%;font-size:24px;font-weight:700}
.offer__note{position:absolute;top:172px;width:100%;font-size:16px;font-weight:600;letter-spacing:.2px}
.slogan{left:43px;top:442px;font-size:19.5px;font-weight:700}
.slogan span{color:var(--red);font-weight:400}
.copy{width:313px;font-size:16.8px;line-height:20.8px;text-align:justify}
.copy--one{left:43px;top:684px;top:485px}
.copy--two{left:43px;top:609px}
.rule{left:34px;top:700px;width:502px;height:2px;background:var(--rule)}
.call{left:77px;top:719px;font-size:14.5px;font-style:italic;font-weight:300;color:var(--grey)}
.phone{left:43px;top:733px;display:flex;align-items:center;gap:6px;font-size:33px;font-weight:700;letter-spacing:.5px}
.divider{left:298px;top:737px;width:1px;height:30px;background:var(--rule)}
.web{left:319px;top:728px;font-size:14.5px;line-height:19px}
.web .domain{color:var(--red)}

/* back */
.services-band{left:0;top:0;width:570px;height:227px}
.services-title{left:190px;top:62px;width:330px;text-align:center;color:#fff;font-size:26px;font-weight:300;letter-spacing:.3px}
.services-title b{font-weight:700}
.services-rule{left:313px;top:111px;width:83px;height:2px;background:#fff}
.hours{left:222px;top:132px;color:#fff;font-size:16px;line-height:21px;font-weight:400;display:grid;grid-template-columns:138px auto}
.body-copy{left:37px;top:256px;width:269px;font-size:14.6px;line-height:18.4px;text-align:justify}
.needle-icon{left:395px;top:258px}
.checks{left:369px;top:360px;list-style:none;font-size:16.5px;line-height:22.8px}
.checks li{display:flex;align-items:center;gap:8px}
.portrait{left:31px;top:622px;width:152px;height:152px;border-radius:50%;background:linear-gradient(160deg,#efe9e6,#b99a89 55%,#8a6a5c)}
.guarantee-line{left:214px;top:660px;width:321px;height:2px;background:var(--red)}
.guarantee{left:262px;top:646px;width:235px;height:31px;border-radius:16px;background:var(--red);color:#fff;font-size:14px;display:flex;align-items:center;justify-content:center;gap:6px}
.contacts{left:224px;top:692px;list-style:none;font-size:19px;line-height:26px}
.contacts li{display:flex;align-items:center;gap:9px}
.find{left:425px;top:707px;width:104px;text-align:center;font-size:13.5px;font-weight:700;letter-spacing:.3px}
.social{left:423px;top:734px;display:flex;gap:2px}
.social span{width:36px;height:36px;border-radius:50%;background:var(--red)}
</style>
</head>
<body>

<section class="page page--front">
  <div class="abs brand"><span class="brand__dot"></span><span class="brand__name">thornbury<br>acupuncture</span></div>
  <p class="abs tagline">THORNBURY ACUPUNCTURE<br>IS <em>SAMPLE TEXT HERE</em></p>

  <svg class="abs hero" viewBox="0 0 570 270" role="img" aria-label="Photo of a practitioner's hands placing an acupuncture needle in a patient's back">
    <defs>
      <linearGradient id="heroTone" x1="0" y1="0" x2="1" y2="1">
        <stop offset="0" stop-color="#fbf7f3"/>
        <stop offset=".45" stop-color="#f3dcc8"/>
        <stop offset="1" stop-color="#dcae8a"/>
      </linearGradient>
    </defs>
    <rect width="570" height="270" fill="url(#heroTone)"/>
    <polygon points="0,0 115,0 0,210" fill="var(--red)" opacity=".85"/>
    <polygon points="0,270 115,0 150,270" fill="#ffffff" opacity=".45"/>
    <polygon points="458,0 570,0 570,225" fill="var(--red)"/>
  </svg>

  <div class="abs offer">
    <p class="offer__lead">Show this flyer<br>and get</p>
    <p class="offer__value">15%</p>
    <p class="offer__off">OFF</p>
    <p class="offer__note">FIRST TREATMENT</p>
  </div>

  <h2 class="abs slogan">SLOGAN HERE <span>SLOGAN HERE</span></h2>
  <p class="abs copy copy--one">Lorem ipsum dolor sit amet, consectetur adipiscing elit. Sed tempus orci turpis, sit amet ultricies tellus aliquet in. Nullam at suscipit nisl, vel interdum est. Vestibulum et placerat ipsum, vitae.</p>
  <p class="abs copy copy--two">Lorem ipsum dolor sit amet, consectetur adipiscing elit. Sed tempus orci turpis, sit amet ultricies tellus aliquet in.</p>

  <div class="abs rule"></div>
  <p class="abs call">Call For A Free Estimate</p>
  <p class="abs phone">
    <svg width="30" height="30" viewBox="0 0 30 30" aria-hidden="true"><circle cx="15" cy="15" r="13" fill="none" stroke="var(--ink)" stroke-width="2.6"/><path d="M10 8.5c1-.8 2-.6 2.5.4l1 2.2c.3.7 0 1.3-.6 1.7l-.8.5c.7 2 2.2 3.6 4.3 4.4l.5-.8c.4-.6 1-.8 1.7-.5l2.2 1c1 .5 1.2 1.5.4 2.5-1.2 1.4-3 1.6-5 .7-3.6-1.7-6-4.3-7.3-7.7-.7-2-.3-3.6 1.1-4.4z" fill="var(--ink)"/></svg>
    888-888-8888
  </p>
  <div class="abs divider"></div>
  <p class="abs web">name@email.com<br><span class="domain">domain.com</span></p>
  <div class="bottom-bar"></div>
</section>

<section class="page page--back">
  <svg class="abs services-band" viewBox="0 0 570 227" role="img" aria-label="Photo of a woman's back with a highlighted area of shoulder pain">
    <defs>
      <linearGradient id="backTone" x1="0" y1="0" x2="1" y2="0">
        <stop offset="0" stop-color="#b8bcc4"/>
        <stop offset="1" stop-color="#ecd9d4"/>
      </linearGradient>
    </defs>
    <rect width="570" height="227" fill="var(--red)"/>
    <polygon points="0,0 211,0 67,227 0,227" fill="url(#backTone)"/>
  </svg>
  <h2 class="abs services-title">OUR <b>SERVICES</b></h2>
  <div class="abs services-rule"></div>
  <div class="abs hours">
    <span>Monday to Friday</span><span>9:00 AM – 7:00 PM</span>
    <span>Saturday</span><span>9:00 AM – 3:00 PM</span>
  </div>

  <p class="abs body-copy">Lorem ipsum dolor sit amet, consectetur adipiscing elit. In iaculis rutrum dignissim. Vestibulum facilisis vulputate cursus. Ut vel nulla eu ante euismod fermentum. Nunc consequat in lectus nec pellentesque. Praesent accumsan accumsan nunc, in condimentum eros cursus et. Vivamus ullamcorper imperdiet porta. Proin interdum sed felis eu viverra. Nam a sollicitudin lectus, a iaculis erat. Aenean ut urna auctor eros pulvinar dictum eget vitae lacus. Suspendisse a dapibus lacus. Integer vel fermentum augue, in mollis tortor. Cras sit amet erat.</p>

  <svg class="abs needle-icon" width="80" height="80" viewBox="0 0 80 80" aria-hidden="true">
    <circle cx="40" cy="40" r="40" fill="var(--red)"/>
    <g stroke="#fff" stroke-width="1.6" stroke-linecap="round" fill="#fff">
      <line x1="38" y1="10" x2="40" y2="70"/><circle cx="38" cy="10" r="2"/>
      <line x1="20" y1="26" x2="38" y2="62"/><circle cx="20" cy="26" r="2"/>
      <line x1="58" y1="26" x2="41" y2="64"/><circle cx="58" cy="26" r="2"/>
    </g>
  </svg>

  <ul class="abs checks">
    <li><svg width="16" height="14" viewBox="0 0 16 14" aria-hidden="true"><path d="M1 7l5 5L15 1" fill="none" stroke="var(--red)" stroke-width="2.4"/></svg>Lorem ipsum</li>
    <li><svg width="16" height="14" viewBox="0 0 16 14" aria-hidden="true"><path d="M1 7l5 5L15 1" fill="none" stroke="var(--red)" stroke-width="2.4"/></svg>Lorem ipsum</li>
    <li><svg width="16" height="14" viewBox="0 0 16 14" aria-hidden="true"><path d="M1 7l5 5L15 1" fill="none" stroke="var(--red)" stroke-width="2.4"/></svg>Lorem ipsum</li>
    <li><svg width="16" height="14" viewBox="0 0 16 14" aria-hidden="true"><path d="M1 7l5 5L15 1" fill="none" stroke="var(--red)" stroke-width="2.4"/></svg>Lorem ipsum</li>
    <li><svg width="16" height="14" viewBox="0 0 16 14" aria-hidden="true"><path d="M1 7l5 5L15 1" fill="none" stroke="var(--red)" stroke-width="2.4"/></svg>Lorem ipsum</li>
  </ul>

  <div class="abs portrait" role="img" aria-label="Portrait photo of the acupuncturist"></div>

  <div class="abs guarantee-line"></div>
  <p class="abs guarantee"><svg width="15" height="13" viewBox="0 0 16 14" aria-hidden="true"><path d="M1 7l5 5L15 1" fill="none" stroke="#fff" stroke-width="2.4"/></svg>100% satisfaction guaranteed</p>

  <ul class="abs contacts">
    <li><svg width="20" height="20" viewBox="0 0 20 20" aria-hidden="true"><path d="M4 2c1-.8 2-.5 2.5.4l1.4 2.6c.4.8.1 1.5-.6 2l-1 .6c.9 2.4 2.7 4.3 5.1 5.2l.6-1c.5-.7 1.2-1 2-.6l2.6 1.4c.9.5 1.200 1.5.4 2.5-1.5 1.8-3.6 2-6 .9C6.8 14.2 4 11.2 2.7 7.3 1.9 5 2.3 3.2 4 2z" fill="none" stroke="var(--ink)" stroke-width="1.4"/></svg>888-888-8888</li>
    <li><svg width="20" height="20" viewBox="0 0 20 20" aria-hidden="true"><rect x="1.5" y="4" width="17" height="12" fill="none" stroke="var(--ink)" stroke-width="1.4"/><path d="M1.5 4l8.5 7 8.5-7" fill="none" stroke="var(--ink)" stroke-width="1.4"/></svg>name@email.com</li>
    <li><svg width="20" height="20" viewBox="0 0 20 20" aria-hidden="true"><path d="M2 10l8-7 8 7M4.5 8v9h4v-5h3v5h4V8" fill="none" stroke="var(--ink)" stroke-width="1.4"/></svg>domain.com</li>
  </ul>

  <p class="abs find">FIND US ON</p>
  <div class="abs social" aria-label="Social media links"><span></span><span></span><span></span></div>
  <div class="bottom-bar"></div>
</section>

</body>
</html>
```